KIRO Nature Soap

We need to design new product Nature and medicative Soap.Made in Malaysia
* 100% natural.
* made from nature Tropic oil.
* Very effective for Acne & Skin irritation
* size 100 Gm.
* Use for all skin types including sensitive skin
* Name of the product " KIRO Soap"

Reason: please I need to extended since I haven't receive any suitable design for my project

Target Market(s)

International

Industry/Entity Type

Hair And Beauty

Font styles to use
Serif

Colors
33a6d7
abd037
fbed22

Requirements
Must have
• * must have English- Arabic ingredient
• * Very effective for Acne & Skin irritation
Nice to have
• * some things related to natural (water,tree,face..)
• * Show faces picture (after - before)

```html
<!DOCTYPE html>
<html lang="en">
<head>
<meta charset="utf-8">
<title>KIRO Soap – Tube Label</title>
<link rel="stylesheet" href="https://fonts.googleapis.com/css2?family=Alegreya:wght@500;700&family=Amiri:wght@700&display=swap">
<style>
  :root {
    --bg: #e4e9ec;
    --band-yellow: #e6e02a;
    --leaf-dark: #1f6a12;
    --leaf-mid: #2f9a1c;
    --leaf-light: #6fd03a;
    --text-white: #ffffff;
    --rule: rgba(255,255,255,0.55);
  }
  html, body {
    margin: 0;
    padding: 0;
    width: 1200px;
    height: 848px;
    overflow: hidden;
    background: var(--bg);
    font-family: "Alegreya", Georgia, serif;
  }
  .canvas {
    position: relative;
    width: 1200px;
    height: 848px;
  }
  .label {
    position: absolute;
    top: 150px;
    width: 340px;
    height: 470px;
    overflow: hidden;
  }
  .label--front { left: 260px; }
  .label--back  { left: 600px; }
  .label__band {
    position: absolute;
    top: 0; left: 0; right: 0;
    height: 24px;
    background: var(--band-yellow);
  }
  .label__photo {
    position: absolute;
    top: 24px; left: 0; right: 0; bottom: 0;
    background:
      radial-gradient(ellipse at 55% 60%, var(--leaf-light) 0%, transparent 55%),
      radial-gradient(ellipse at 30% 25%, var(--leaf-mid) 0%, transparent 60%),
      linear-gradient(180deg, var(--leaf-dark) 0%, var(--leaf-mid) 55%, var(--leaf-dark) 100%);
  }
  .label__text {
    position: absolute;
    left: 0; right: 0;
    margin: 0;
    color: var(--text-white);
    text-shadow: 0 1px 3px rgba(0,0,0,0.35);
  }
  .brand {
    top: 82px;
    text-align: center;
    font-weight: 700;
    line-height: 0.95;
  }
  .brand__name { display: block; font-size: 58px; letter-spacing: 1px; }
  .brand__product { display: block; font-size: 56px; }
  .weight {
    top: 362px;
    text-align: center;
    font-size: 25px;
    font-weight: 700;
  }
  .origin {
    top: 420px;
    text-align: center;
    font-size: 17px;
    font-weight: 700;
  }
  .benefits {
    top: 108px;
    left: 24px;
    right: 16px;
    padding: 0;
    list-style: none;
    font-size: 17px;
    font-weight: 700;
    line-height: 31px;
  }
  .ingredients {
    top: 290px;
    left: 24px;
    right: 24px;
    padding-top: 10px;
    border-top: 1px solid var(--rule);
    font-size: 13px;
    font-weight: 500;
    line-height: 18px;
  }
  .ingredients__title {
    display: block;
    font-weight: 700;
    font-size: 14px;
    margin-bottom: 2px;
  }
  .ingredients__ar {
    margin-top: 10px;
    font-family: "Amiri", "Times New Roman", serif;
    font-weight: 700;
    font-size: 15px;
    line-height: 22px;
    text-align: right;
  }
</style>
</head>
<body>
<main class="canvas">
  <section class="label label--front">
    <div class="label__band"></div>
    <div class="label__photo" role="img" aria-label="Close-up photograph of fresh green leaves with water droplets"></div>
    <h1 class="label__text brand">
      <span class="brand__name">KIRO</span>
      <span class="brand__product">Soap</span>
    </h1>
    <p class="label__text weight">100 Gm</p>
    <p class="label__text origin">Made in Malaysia</p>
  </section>

  <section class="label label--back">
    <div class="label__band"></div>
    <div class="label__photo" role="img" aria-label="Close-up photograph of fresh green leaves with water droplets"></div>
    <ul class="label__text benefits">
      <li>Made from nature Tropic oil.</li>
      <li>Very effective for</li>
      <li>Acne &amp; Skin irritation</li>
      <li>Use for all skin types</li>
      <li>including sensitive skin</li>
    </ul>
    <div class="label__text ingredients">
      <p style="margin:0;" lang="en">
        <span class="ingredients__title">Ingredients</span>
        Tropic palm oil, coconut oil, glycerin, aloe leaf extract, water.
      </p>
      <p class="ingredients__ar" lang="ar" dir="rtl" style="margin-bottom:0;">
        المكونات: زيت النخيل الاستوائي، زيت جوز الهند، جلسرين، خلاصة أوراق الصبار، ماء.
      </p>
    </div>
  </section>
</main>
</body>
</html>
```